Tindale Farm Brochure

To design a small brochure that tells people about our U-Pick cherry farm, where we are, when we are open and what our contact details are.

We have existing logo's which should be used. I have uploaded a file with these details.

Details about us are all located on:-
www.pagelinkhub.example/tindalefarm
https://circles.socialnook.example/u/0/b/507719364028815530947/507719364028815530947/about/p/pub

```html
<!DOCTYPE html>
<html lang="en">
<head>
<meta charset="utf-8">
<title>Tindale Farm Brochure</title>
<link rel="stylesheet" href="https://fonts.googleapis.com/css2?family=Exo:wght@400;600&display=swap">
<style>
  :root {
    --page-bg: #e9e9e9;
    --cream-top: #e2eba4;
    --cream-bottom: #ffffff;
    --teal: #19a886;
    --lime: #a4c93a;
    --text-teal: #1f9e7c;
    --text-strong: #15896b;
    --brand-green: #3b9a5a;
  }
  * { margin: 0; padding: 0; box-sizing: border-box; }
  html, body {
    width: 872px; height: 1200px; overflow: hidden;
    background: var(--page-bg);
    font-family: "Exo", sans-serif;
  }
  .brochure {
    position: absolute; left: 5.5px; top: 12.5px;
    width: 615px; height: 839px;
    transform: scale(1.4); transform-origin: 0 0;
    background: linear-gradient(to bottom, var(--cream-top) 0%, var(--cream-bottom) 68%);
    overflow: hidden;
    color: var(--text-teal);
  }
  .decor { position: absolute; inset: 0; }
  .brand {
    position: absolute; top: 56px; left: 0; width: 100%;
    text-align: center; color: var(--brand-green); font-weight: 600; line-height: 1;
  }
  .brand-name { display: block; font-size: 62px; letter-spacing: 1px; }
  .brand-sub { display: block; font-size: 40px; margin-top: 4px; }
  .intro, .pricing {
    position: absolute; left: 0; width: 100%;
    text-align: center; font-size: 18.5px; line-height: 23.5px; letter-spacing: 0.9px;
  }
  .intro { top: 198px; }
  .pricing { top: 300px; }
  .strong { color: var(--text-strong); font-weight: 600; }
  .varieties {
    position: absolute; left: 66px; top: 404px;
    font-size: 18.5px; line-height: 24px; letter-spacing: 0.9px;
  }
  .quote {
    position: absolute; left: 65px; top: 486px; width: 400px;
    font-size: 14.5px; line-height: 18px; letter-spacing: 0.6px;
    font-weight: 600; color: var(--text-strong);
  }
  .quote cite { display: block; text-align: right; font-style: normal; }
  .contacts { position: absolute; left: 66px; top: 567px; list-style: none; }
  .contact { display: flex; align-items: center; margin-bottom: 10px; }
  .contact-icon {
    width: 22px; height: 22px; border-radius: 3px; background: var(--lime);
    flex: none; margin-right: 25px;
  }
  .contact-icon svg { display: block; }
  .contact-text { font-size: 20px; line-height: 22px; letter-spacing: 0.6px; }
  .contact-text.email { letter-spacing: 0; }
  .contact-text.address { font-size: 16.5px; line-height: 19px; letter-spacing: 0.6px; }
</style>
</head>
<body>
<main class="brochure">
  <svg class="decor" width="615" height="839" viewBox="0 0 615 839" aria-hidden="true">
    <path d="M0,125 Q55,40 140,0 L0,0Z" fill="var(--lime)"/>
    <path d="M0,108 Q30,30 95,0 L0,0Z" fill="var(--teal)"/>
    <path d="M0,808 C300,790 500,700 615,288 L615,839 L0,839Z" fill="var(--lime)"/>
    <path d="M0,823 C320,805 530,720 615,448 L615,839 L0,839Z" fill="var(--teal)"/>
  </svg>

  <h1 class="brand">
    <span class="brand-name">Tindale</span>
    <span class="brand-sub">Farm</span>
  </h1>

  <p class="intro">Tindale Farm is in the beautiful Yarra Valley,<br>
    an ideal location for growing sweet juicy cherries.<br>
    <span class="strong">Visit us for Pick Your Own or Pre-Picked Cherries.</span></p>

  <p class="pricing">When picking, you can eat as much as you want.<br>
    Prices for take away U-Pick fruit is $8 per kilo.<br>
    <span class="strong">There are no entry fees.</span></p>

  <p class="varieties">We have 12 varieties of cherries, most of which are<br>
    heritage varieties and are rarely found elsewhere.</p>

  <blockquote class="quote">"It's the magnificent views and our happy trees.<br>
    That's what makes our cherries juicier and sweeter."
    <cite>Farmer Ned.</cite></blockquote>

  <ul class="contacts">
    <li class="contact">
      <span class="contact-icon"><svg width="22" height="22" viewBox="0 0 22 22"><path d="M11,4 a5,5 0 0 1 5,5 c0,4 -5,9 -5,9 s-5,-5 -5,-9 a5,5 0 0 1 5,-5z" fill="none" stroke="#fff" stroke-width="1.6"/><circle cx="11" cy="9" r="1.8" fill="#fff"/></svg></span>
      <span class="contact-text address">18 Ridgeway Orchard Road,<br>Tindale VIC 3188</span>
    </li>
    <li class="contact">
      <span class="contact-icon"><svg width="22" height="22" viewBox="0 0 22 22"><rect x="4" y="6" width="14" height="10" fill="none" stroke="#fff" stroke-width="1.4"/><path d="M4,6 L11,12 L18,6" fill="none" stroke="#fff" stroke-width="1.4"/></svg></span>
      <span class="contact-text email">ned@orchardmail.example</span>
    </li>
    <li class="contact">
      <span class="contact-icon"></span>
      <span class="contact-text">tindalefarm</span>
    </li>
    <li class="contact">
      <span class="contact-icon"><svg width="22" height="22" viewBox="0 0 22 22"><path d="M7,4 L9.5,4 L10.5,8 L8.8,9.3 Q10,12.5 12.7,13.2 L14,11.5 L18,12.5 L18,15 Q17,18 13,17 Q6,14.5 4.5,8 Q4,5 7,4Z" fill="#fff"/></svg></span>
      <span class="contact-text">1300 555 014</span>
    </li>
  </ul>
</main>
</body>
</html>
```